Parcelwise HQ letterhead and envelope

Design a formal (8.5x11) letterhead and envelope for sales outreach and legal matters. Using design input from https://www.parcelwisehq.example/ and the attached documents.

Industry/Entity Type

Software Service

Requirements
Must have
• These 4 hex colors are our official colors:
• #355c98 [blue]
• #1eb1a2 [teal]
• #fdba12 [gold]
• #f1653b [orange]
• So no other colors besides these should be used.

```html
<!DOCTYPE html>
<html lang="en">
<head>
<meta charset="utf-8">
<title>Parcelwise HQ letterhead and envelope</title>
<link rel="stylesheet" href="https://fonts.googleapis.com/css2?family=Open+Sans:wght@400;600;700&display=swap">
<style>
  :root {
    --brand-blue: #355c98;
    --brand-teal: #1eb1a2;
    --paper: #f6f6f7;
    --backdrop: #e2e2e3;
    --ink: #7a7a7c;
    --ink-dark: #3e3e40;
    --rule: #c9c9cc;
  }
  * { box-sizing: border-box; margin: 0; padding: 0; }
  html, body { width: 1200px; height: 825px; overflow: hidden; }
  body {
    background: var(--backdrop);
    font-family: "Open Sans", Arial, sans-serif;
    position: relative;
  }
  .letterhead, .envelope {
    position: absolute;
    background: var(--paper);
    overflow: hidden;
  }
  .letterhead { left: 81px; top: 82px; width: 467px; height: 660px; }

  .brand {
    position: absolute;
    display: flex;
    align-items: center;
    gap: 8px;
    color: var(--brand-blue);
    font-size: 20px;
    font-weight: 400;
    letter-spacing: 0.2px;
  }
  .brand-dot {
    width: 22px; height: 22px;
    border: 2px solid var(--brand-blue);
    border-radius: 50%;
  }
  .letterhead .brand { left: 32px; top: 27px; }

  .contact {
    position: absolute;
    right: 37px; top: 31px;
    font-size: 8px;
    line-height: 10px;
    color: var(--ink-dark);
  }
  .contact li { list-style: none; display: flex; align-items: center; gap: 3px; }
  .contact svg { width: 6px; height: 6px; fill: var(--brand-blue); }

  .letter-body {
    position: absolute;
    left: 38px; top: 140px;
    width: 392px;
  }
  .salutation { font-size: 11.5px; font-weight: 700; color: var(--ink-dark); margin-bottom: 12px; }
  .letter-body p {
    font-size: 9.4px;
    line-height: 12.2px;
    color: var(--ink);
    text-align: justify;
    margin-bottom: 12px;
  }
  .signature {
    position: absolute;
    left: 38px; top: 462px;
    width: 88px; height: 42px;
    background: linear-gradient(135deg, #e6e6e8, #d8d8db);
    border-radius: 3px;
  }

  .footer-band {
    position: absolute;
    left: 0; bottom: 0;
    width: 100%; height: 22px;
    background: var(--brand-blue);
  }
  .footer-address {
    position: absolute;
    bottom: 5px;
    font-size: 8px;
    color: #fff;
  }
  .footer-address b { font-weight: 700; }
  .letterhead .footer-address { left: 41px; }
  .web-tab {
    position: absolute;
    bottom: 4px;
    width: 134px; height: 18px;
  }
  .web-tab svg { position: absolute; inset: 0; width: 100%; height: 100%; }
  .web-tab span {
    position: relative;
    display: block;
    text-align: center;
    font-size: 7.6px;
    letter-spacing: 0.6px;
    color: #fff;
    line-height: 13px;
  }
  .letterhead .web-tab { left: 306px; }

  .envelope-flap {
    position: absolute;
    left: 584px; top: 441px;
    width: 537px; height: 70px;
  }
  .envelope { left: 584px; top: 510px; width: 537px; height: 232px; }
  .envelope .brand { left: 32px; top: 25px; }
  .flap-mark {
    position: absolute;
    left: 837px; top: 460px;
    width: 34px; height: 34px;
    border: 2.5px solid #fff;
    border-radius: 50%;
  }
  .faint-circle {
    position: absolute;
    left: 322px; top: -2px;
    width: 214px; height: 214px;
    border: 12px solid #ececee;
    border-radius: 50%;
  }
  .address-window {
    position: absolute;
    left: 35px; top: 116px;
    width: 206px; height: 60px;
    background: #f1f1f2;
    border-radius: 4px;
    padding: 14px 8px 0;
  }
  .address-window i {
    display: block;
    border-top: 1px dotted var(--rule);
    height: 11px;
  }
  .envelope .footer-address { left: 39px; }
  .envelope .web-tab { left: 360px; }
</style>
</head>
<body>

<section class="letterhead">
  <div class="brand"><span class="brand-dot"></span>Parcelwise HQ</div>

  <ul class="contact">
    <li><svg viewBox="0 0 10 10"><path d="M2 0h2l1 3-1.5 1a6 6 0 0 0 2.5 2.5L7 5l3 1v2a2 2 0 0 1-2 2A8 8 0 0 1 0 2a2 2 0 0 1 2-2z"/></svg>(555) 014-2290</li>
    <li><svg viewBox="0 0 10 10"><path d="M0 2h10v6H0z"/></svg>jsmith@parcelwisehq.example</li>
  </ul>

  <div class="letter-body">
    <p class="salutation">Dear Mr. Avery,</p>
    <p>Lorem Ipsum is simply dummy text of the printing and typesetting industry. Lorem Ipsum has been the industry's standard dummy text ever since the 1500s, when an unknown printer took a galley of type and scrambled it to make a type specimen book. It has survived not only five centuries, but also the leap into electronic typesetting, remaining essentially unchanged.</p>
    <p>The standard chunk of Lorem Ipsum used since the 1500s is reproduced below for those interested. Sections 1.10.32 and 1.10.33 from "de Finibus Bonorum et Malorum" by Cicero are also reproduced in their exact original form, accompanied by English versions from the 1914 translation by H. Rackham</p>
    <p>Lorem Ipsum is simply dummy text of the printing and typesetting industry. Lorem Ipsum has been the industry's standard dummy text ever since the 1500s, when an unknown printer took a galley of type and scrambled it to make a type specimen book. It has survived not only five centuries, but also the leap into electronic typesetting, remaining essentially unchanged. It was popularised in the</p>
    <p>Lorem Ipsum is simply dummy text of the printing and typesetting industry. Lorem Ipsum has been the industry's standard dummy text ever since the 1500s, when an unknown printer took a galley of type and scrambled it to make a type specimen book. It has survived not only five centuries, but also the leap into electronic typesetting, remaining essentially unchanged. It was popularised in the</p>
  </div>

  <div class="signature" role="img" aria-label="Handwritten signature of the sender"></div>

  <div class="footer-band"></div>
  <p class="footer-address"><b>Parcelwise HQ</b> 42 Harbor Lane Lakeside, MI 00000</p>
  <div class="web-tab">
    <svg viewBox="0 0 134 18" preserveAspectRatio="none"><path d="M0 0h134l-10 11q-5 7-14 7H24q-9 0-14-7z" fill="var(--brand-teal)" stroke="#fff" stroke-width="1.2"/></svg>
    <span>www.parcelwisehq.example</span>
  </div>
</section>

<svg class="envelope-flap" viewBox="0 0 537 70" preserveAspectRatio="none">
  <path d="M0 70L8 50Q14 40 40 36L300 1Q337 -2 374 2L500 38Q528 42 532 56L537 70z" fill="var(--brand-blue)"/>
</svg>
<div class="flap-mark"></div>

<section class="envelope">
  <div class="faint-circle"></div>
  <div class="brand"><span class="brand-dot"></span>Parcelwise HQ</div>
  <div class="address-window"><i></i><i></i><i></i><i></i></div>

  <div class="footer-band"></div>
  <p class="footer-address"><b>Parcelwise HQ</b> 42 Harbor Lane Lakeside, MI 00000</p>
  <div class="web-tab">
    <svg viewBox="0 0 134 18" preserveAspectRatio="none"><path d="M0 0h134l-10 11q-5 7-14 7H24q-9 0-14-7z" fill="var(--brand-teal)" stroke="#fff" stroke-width="1.2"/></svg>
    <span>www.parcelwisehq.example</span>
  </div>
</section>

</body>
</html>
```